Brightmill Data Works

Our company is about IT hardwares and IT solutions. IT hardware such as PC, RAMS, storage and servers. IT solutions such as project management, BA. We are also selling new technology too.

Target Market(s)

Consumer, Small to Medium Business, Corporate

Requirements
Must have
• The business card must have the following:
• Name:
• Title:
• Contact Number:
• Email address:
• Website:
• Color: Must match the logo color upgrade

```html
<!DOCTYPE html>
<html lang="en">
<head>
<meta charset="utf-8">
<title>Brightmill Data Works — Business Card</title>
<link rel="stylesheet" href="https://fonts.googleapis.com/css2?family=Saira+Semi+Condensed:wght@400;700&display=swap">
<style>
  :root {
    --backdrop: #d9d9d9;
    --card-light: #dcdcdc;
    --charcoal: #3e3e3e;
    --rust: #a65a24;
    --rust-text: #b0642a;
    --ink: #1f1f1f;
    --mist: #e6e6e6;
  }
  * { margin: 0; padding: 0; box-sizing: border-box; }
  html, body {
    width: 1200px; height: 878px; overflow: hidden;
    background: var(--backdrop);
    font-family: "Saira Semi Condensed", sans-serif;
  }
  .canvas { position: relative; width: 1200px; height: 878px; }
  .card {
    position: absolute; top: 139px;
    width: 423px; height: 746px;
    transform: scale(0.8); transform-origin: top left;
    background: var(--card-light);
    overflow: hidden;
  }
  .card--front { left: 230px; }
  .card--back { left: 598px; }
  .card__art { position: absolute; inset: 0; width: 423px; height: 746px; }
  .wordmark {
    position: absolute; left: 0; width: 100%;
    text-align: center; font-weight: 700; text-transform: uppercase;
    line-height: 1.0; letter-spacing: 1px;
  }
  .card--front .wordmark { top: 128px; font-size: 46px; color: var(--mist); }
  .card--back .wordmark { top: 455px; left: 0; width: 315px; font-size: 46px; color: var(--charcoal); }
  .person { position: absolute; top: 428px; width: 100%; text-align: center; }
  .person__name { font-size: 38px; font-weight: 400; color: var(--charcoal); line-height: 1.05; letter-spacing: 0.5px; }
  .person__title { font-size: 32px; font-weight: 400; color: var(--rust-text); line-height: 1.1; }
  .contact { position: absolute; top: 570px; width: 100%; list-style: none; text-align: center; }
  .contact li { font-size: 27px; color: var(--ink); line-height: 44px; letter-spacing: 0.5px; }
</style>
</head>
<body>
<main class="canvas">

  <section class="card card--front" aria-label="Business card front">
    <svg class="card__art" viewBox="0 0 423 746" aria-hidden="true">
      <polygon fill="var(--rust)" points="0,0 423,0 423,425 255,350 200,410 0,290"/>
      <polygon fill="var(--charcoal)" points="0,0 235,0 423,62 423,160 200,410 0,65"/>
    </svg>
    <div class="wordmark">Brightmill<br>Data Works</div>
    <div class="person">
      <p class="person__name">DANA WHITLOW</p>
      <p class="person__title">MANAGER</p>
    </div>
    <ul class="contact">
      <li>+1-555-014-2290</li>
      <li>dana@brightmilldata.com</li>
      <li>www.brightmilldata.com</li>
    </ul>
  </section>

  <section class="card card--back" aria-label="Business card back">
    <svg class="card__art" viewBox="0 0 423 746" aria-hidden="true">
      <polygon fill="var(--charcoal)" points="122,0 423,0 423,746 235,746 330,510"/>
      <polygon fill="var(--rust)" points="134,0 423,0 423,305 340,505"/>
      <polygon fill="var(--rust)" points="340,520 423,720 423,746 247,746"/>
    </svg>
    <div class="wordmark">Brightmill<br>Data Works</div>
  </section>

</main>
</body>
</html>
```